Business cards in digital learning for freelancer

Hello, I need a business cards in french. I work in the Digital learning industries as freeelancer; I'm an expert in digital learning. I work in France. My customer are in the health industry, pharmaceutical industry, and training organization. I've got a logo. I offer three services: consulting, Design, and Training. In the consulting, I offers coaching to choose your digital learning tools and the digital learning strategy. For the Design, I product differents level of elearning like rapid-learning, elearning, micro-learning, video-learning. And for the training service, I've create training about pedagogy, digital learning management project, Digital learning design.
I join my Logo create in this platform. My universe is gamified. I like the life, and I'm very social. I want a card like I'm I. I love Art (painting), Europeen comics. I use in my visual support "permanent maker" font and caracters. I would like cards: elegant, modern, Top class. If you need any information, you can ask me.
thanks for ideas

Target Market(s)

in health industries and training organization for Training manager, instructor, human resources director

Contact Information for Business Card

Phone number : 06 71 38 95 14 , mail: bastiengolmier@quelmoto.fr, web: bastiengolmier.fr , Carrivo

Font styles to use
Sans Serif

Requirements
Must have
• Use my logo and write my 3 services (consulting, training, design)

```html
<!DOCTYPE html>
<html lang="fr">
<head>
<meta charset="utf-8">
<title>Bastien Golmier – Cartes de visite</title>
<link rel="stylesheet" href="https://fonts.googleapis.com/css2?family=Arimo:wght@400;700&family=Cinzel:wght@400;600&display=swap">
<style>
  :root {
    --backdrop: #1b1b1c;
    --kraft-light: #dfbf91;
    --kraft-mid: #c79e6c;
    --kraft-dark: #a7794b;
    --ink: #141210;
    --paper-icon: #e7cfa6;
  }
  * { margin: 0; padding: 0; box-sizing: border-box; }
  html, body {
    width: 1093px; height: 1200px; overflow: hidden;
    background: var(--backdrop);
  }
  .sheet { position: relative; width: 1093px; height: 1200px; }
  .card {
    position: absolute; left: 264px; width: 580px; height: 357px;
    background: linear-gradient(135deg, var(--kraft-light) 0%, var(--kraft-mid) 50%, var(--kraft-dark) 100%);
    color: var(--ink);
    font-family: "Arimo", Arial, sans-serif;
    text-align: center;
  }
  .card--front { top: 226px; }
  .card--back { top: 620px; }

  .holder-name {
    position: absolute; top: 64px; left: 0; right: 0;
    font-family: "Cinzel", "Times New Roman", serif;
    font-weight: 600; font-size: 25px; letter-spacing: 0.5px;
  }
  .holder-role {
    position: absolute; top: 96px; left: 0; right: 0;
    font-size: 18px;
  }
  .divider {
    position: absolute; left: 0; right: 0;
    display: flex; align-items: center; justify-content: center; gap: 4px;
  }
  .divider__line { height: 1.5px; background: var(--ink); }
  .divider--icons { top: 136px; }
  .divider--icons .divider__line { width: 56px; }
  .divider--icons .divider__line:first-child { margin-right: 2px; }
  .divider--icons .divider__line:last-child { margin-left: 2px; }
  .contact-icon {
    width: 27px; height: 27px; border-radius: 3px;
    background: var(--ink);
    display: flex; align-items: center; justify-content: center;
  }
  .contact-icon svg { width: 17px; height: 17px; }

  .contact-list {
    position: absolute; top: 174px; left: 0; right: 0;
    list-style: none; font-size: 18.5px; line-height: 23.5px;
  }

  .divider--social { top: 258px; gap: 8px; }
  .divider--social .divider__line { width: 80px; height: 1px; }
  .social-name { font-weight: 700; font-size: 16px; }

  .brand-mark {
    position: absolute; top: 92px; left: 50%; width: 70px; height: 70px;
    margin-left: -35px; border-radius: 50%; background: var(--ink);
  }
  .brand-name {
    position: absolute; top: 180px; left: 0; right: 0;
    font-weight: 700; font-size: 40px; letter-spacing: 2px; line-height: 1;
  }
  .brand-tagline {
    position: absolute; top: 242px; left: 0; right: 0;
    display: flex; align-items: center; justify-content: center; gap: 8px;
    font-family: "Cinzel", "Times New Roman", serif; font-size: 13px; letter-spacing: 1px;
  }
  .brand-tagline .divider__line { width: 54px; height: 1px; }
  .services {
    position: absolute; top: 268px; left: 0; right: 0;
    font-size: 15.5px; letter-spacing: 0.3px;
    display: flex; justify-content: center; align-items: center; gap: 9px;
  }
  .services__dot { width: 8px; height: 8px; border-radius: 50%; background: var(--ink); }
</style>
</head>
<body>
<main class="sheet">

  <section class="card card--front" aria-label="Recto">
    <h1 class="holder-name">Bastien Golmier</h1>
    <p class="holder-role">Managing Director</p>

    <div class="divider divider--icons">
      <span class="divider__line"></span>
      <span class="contact-icon" aria-label="Téléphone">
        <svg viewBox="0 0 20 20" fill="var(--paper-icon)">
          <path d="M2 7c0-2 3-3 8-3s8 1 8 3v1.5h-4V7H6v1.5H2z"/>
          <path d="M5 10h10l1.5 6h-13z"/>
        </svg>
      </span>
      <span class="contact-icon" aria-label="E-mail">
        <svg viewBox="0 0 20 20" fill="none" stroke="var(--paper-icon)" stroke-width="1.3">
          <rect x="2" y="4.5" width="16" height="11"/>
          <path d="M2 4.5l8 6.5 8-6.5M2 15.5l6-5M18 15.5l-6-5"/>
        </svg>
      </span>
      <span class="contact-icon" aria-label="Site web">
        <svg viewBox="0 0 20 20">
          <circle cx="10" cy="10" r="8" fill="var(--paper-icon)"/>
          <path d="M7 5c2 0 3 2 2 3s-3 1-2 3 3 1 2 4" stroke="var(--ink)" stroke-width="2" fill="none"/>
        </svg>
      </span>
      <span class="divider__line"></span>
    </div>

    <ul class="contact-list">
      <li>06 71 38 95 14</li>
      <li>bastiengolmier@quelmoto.fr</li>
      <li>www.bastiengolmier.fr</li>
    </ul>

    <div class="divider divider--social">
      <span class="divider__line"></span>
      <span class="social-name">Carrivo</span>
      <span class="divider__line"></span>
    </div>
  </section>

  <section class="card card--back" aria-label="Verso">
    <span class="brand-mark" aria-hidden="true"></span>
    <p class="brand-name">GOLMIER</p>
    <p class="brand-tagline">
      <span class="divider__line"></span>
      DIGITAL LEARNING
      <span class="divider__line"></span>
    </p>
    <p class="services">
      <span>CONSULTING</span><span class="services__dot"></span>
      <span>TRAINING</span><span class="services__dot"></span>
      <span>DESIGN</span>
    </p>
  </section>

</main>
</body>
</html>
```